Create Design for 750ml Bottle of THC Coconut Rum

Our Brand, Sippin' Pals, is looking to create a new 750ml bottle design for a new Coconut Rum THC drink. It would have the same "feel" as Corvala Rum but use our logo and have the title "Lazy Tide".

We would like the bottle to be white, and have palm trees - probably in a circle similar to Corvala but with our own flare.

The Bottle needs to say: "Coconut Rum" and "Lazy Tide"

See images for our logo, sample of a Corvala bottle, and some of our current canned drinks.

Target Market(s)

21+ Social THC Beverage users, typically 30-60years of age

Industry/Entity Type

THC Beverages

Font styles to use
Other font styles liked:
• SantEliaScript, Gotham

Colors
59FF00
82FF00
B8FF75
E3FFCB
F4FFEA

Requirements
Must have
• The Sippin Pals Logo, Palm trees, and the Words: Lazy Tide and Coconut Rum
Nice to have
• We like the design by Corvala but need to have our own design and incorporate our logo
Should not have
• Extra Hemp Leaves, overly complicated or busy designs

```html
<!DOCTYPE html>
<html lang="en">
<head>
<meta charset="utf-8">
<title>Sippin' Pals – Coconut Rum and Lazy Tide</title>
<link rel="stylesheet" href="https://fonts.googleapis.com/css2?family=Oswald:wght@600&family=Pacifico&family=Montserrat:wght@500;700&display=swap">
<style>
  :root {
    --bg: #ffffff;
    --label-green: #1f9e1a;
    --brand-white: #ffffff;
    --palm-pale: #d9f5c8;
    --palm-light: #8ee06a;
    --palm-mid: #45bd3c;
    --palm-deep: #24902a;
    --ink-grey: #555555;
  }
  * { margin: 0; padding: 0; box-sizing: border-box; }
  html, body {
    width: 1200px;
    height: 1200px;
    overflow: hidden;
    background: var(--bg);
  }
  .label {
    position: relative;
    width: 1200px;
    height: 1200px;
  }
  .label > * {
    position: absolute;
    left: 0;
    width: 1200px;
    text-align: center;
  }
  .tagline {
    top: 98px;
    font-family: "Oswald", sans-serif;
    font-weight: 600;
    font-size: 64px;
    line-height: 1;
    color: var(--label-green);
  }
  .palm-badge {
    top: 196px;
    height: 520px;
    display: flex;
    justify-content: center;
  }
  .palm-badge svg { display: block; }
  .brand-name {
    top: 514px;
    font-family: "Oswald", sans-serif;
    font-weight: 600;
    font-size: 72px;
    line-height: 1;
    color: var(--brand-white);
  }
  .product-name {
    top: 742px;
    font-family: "Pacifico", cursive;
    font-weight: 400;
    color: var(--label-green);
    line-height: 1;
  }
  .product-name .line {
    display: block;
    font-size: 74px;
    height: 82px;
    line-height: 82px;
  }
  .product-name .joiner {
    display: flex;
    align-items: center;
    justify-content: center;
    gap: 26px;
    font-size: 64px;
    height: 76px;
    line-height: 76px;
  }
  .product-name .joiner::before,
  .product-name .joiner::after {
    content: "";
    width: 128px;
    height: 5px;
    margin-top: 10px;
    background: var(--label-green);
  }
  .origin {
    top: 1040px;
    font-family: "Montserrat", sans-serif;
    font-weight: 700;
    font-size: 28px;
    letter-spacing: 5px;
    line-height: 1;
    color: var(--ink-grey);
  }
  .dosage {
    top: 1078px;
    font-family: "Montserrat", sans-serif;
    font-weight: 500;
    font-size: 18px;
    line-height: 1;
    color: var(--ink-grey);
  }
</style>
</head>
<body>
  <main class="label">
    <p class="tagline">“TASTE THE NEW BUZZ”</p>

    <div class="palm-badge" role="img" aria-label="Illustration of tropical palm trees leaning around a round green badge with rolling green hills">
      <svg width="600" height="520" viewBox="0 0 600 520" aria-hidden="true">
        <defs>
          <radialGradient id="palmGlow" cx="50%" cy="50%" r="50%">
            <stop offset="0%" stop-color="var(--palm-light)" stop-opacity="0.55"/>
            <stop offset="100%" stop-color="var(--palm-pale)" stop-opacity="0"/>
          </radialGradient>
          <radialGradient id="badgeTone" cx="50%" cy="40%" r="62%">
            <stop offset="0%" stop-color="var(--palm-light)"/>
            <stop offset="55%" stop-color="var(--palm-mid)"/>
            <stop offset="100%" stop-color="var(--palm-deep)"/>
          </radialGradient>
        </defs>
        <ellipse cx="300" cy="200" rx="300" ry="200" fill="url(#palmGlow)"/>
        <circle cx="300" cy="276" r="242" fill="url(#badgeTone)"/>
      </svg>
    </div>

    <p class="brand-name">SIPPIN' PALS</p>

    <h1 class="product-name">
      <span class="line">Coconut Rum</span>
      <span class="joiner">and</span>
      <span class="line">Lazy Tide</span>
    </h1>

    <p class="origin">IMPORTED</p>
    <p class="dosage">5 MG OF DELTA 9 THC + 5MG CBG</p>
  </main>
</body>
</html>
```